Finance and accounting business advisory and consulting

I am a one person finance and accounting advisory businessI would like to include imagery of astrology Taurus glyph. Taurus which represents abundance. The name of the business VelmoRix is like Taurus Finance. It is based on the bull, strong. I would like the F in VelmonRix to be capitalised or so that the Fin stands outThe business aims to build stable long term growth for clientsColours should be green and gold like an Australian dollar $100 or $50, not kermit green or fluro green or shiny gold. The gold should be the accent. Can also have brown on the bottom like solid earth.Words that describe VelmoRix are: Harmony; Devotion; Values; Reliable; Perseverance; Stable; Responsiveness; Loyal; Trustworthy
Industry/Entity Type
Accounting
Contact Information for Business Card
Alex AndersonDirectorTauroFin Pty. Ltd.Finance and AccountingM: 0407 160 201E: brentwhitlow.rix@mailpost.example

```html
<!DOCTYPE html>
<html lang="en">
<head>
<meta charset="utf-8">
<title>VelmoRix – Business Card</title>
<link rel="stylesheet" href="https://fonts.googleapis.com/css2?family=Open+Sans:wght@300;400;600&display=swap">
<style>
  :root {
    --page-bg: #efe9dc;
    --card-gold-light: #f3e9b0;
    --card-gold: #e2c45a;
    --card-gold-deep: #c99a2e;
    --card-edge: #a97a22;
    --circle-soft: rgba(255, 250, 220, 0.45);
    --circle-green: rgba(214, 222, 120, 0.45);
    --ink: #1c1a14;
    --ink-muted: #3a362a;
    --tag-ink: #5a5648;
  }
  * { margin: 0; padding: 0; box-sizing: border-box; }
  html, body {
    width: 1200px;
    height: 1000px;
    overflow: hidden;
    background: var(--page-bg);
    font-family: "Open Sans", Arial, sans-serif;
  }
  .business-card {
    position: absolute;
    left: 100px;
    top: 210px;
    width: 1000px;
    height: 580px;
    border-radius: 6px;
    overflow: hidden;
    background: linear-gradient(125deg, var(--card-gold-deep) 0%, var(--card-gold) 30%, var(--card-gold-light) 55%, var(--card-gold) 80%, var(--card-gold-deep) 100%);
    box-shadow: 0 0 0 6px var(--card-edge) inset, 0 18px 40px rgba(60, 40, 10, 0.25);
  }
  .background-circles { position: absolute; inset: 0; }
  .brand-block {
    position: absolute;
    left: 90px;
    top: 250px;
    display: flex;
    flex-direction: column;
    align-items: flex-start;
    gap: 22px;
  }
  .brand-name {
    display: flex;
    align-items: center;
    gap: 18px;
    font-size: 58px;
    font-weight: 300;
    letter-spacing: 4px;
    color: var(--ink-muted);
    text-transform: uppercase;
  }
  .brand-dot {
    width: 64px;
    height: 64px;
    border-radius: 50%;
    background: var(--ink-muted);
  }
  .brand-tagline {
    margin-left: 82px;
    padding: 6px 4px;
    border-top: 2px dashed var(--tag-ink);
    border-bottom: 2px dashed var(--tag-ink);
    font-size: 22px;
    font-weight: 600;
    line-height: 1.05;
    letter-spacing: 2px;
    color: var(--tag-ink);
    text-transform: uppercase;
  }
  .contact-block {
    position: absolute;
    right: 70px;
    top: 70px;
    text-align: right;
    color: var(--ink);
    text-transform: uppercase;
  }
  .contact-name {
    font-size: 46px;
    font-weight: 400;
    letter-spacing: 2px;
    padding-bottom: 8px;
    border-bottom: 2px dashed var(--ink);
    margin-bottom: 12px;
  }
  .contact-role,
  .contact-line {
    font-size: 20px;
    font-weight: 400;
    letter-spacing: 2px;
    line-height: 1.6;
  }
</style>
</head>
<body>
  <section class="business-card" aria-label="VelmoRix business card">
    <svg class="background-circles" width="1000" height="580" viewBox="0 0 1000 580" aria-hidden="true">
      <circle cx="230" cy="380" r="270" fill="var(--circle-green)"/>
      <circle cx="290" cy="170" r="210" fill="var(--circle-soft)"/>
      <circle cx="740" cy="330" r="250" fill="var(--circle-soft)"/>
      <circle cx="900" cy="120" r="170" fill="var(--circle-green)"/>
    </svg>

    <div class="brand-block">
      <div class="brand-name"><span class="brand-dot"></span>VelmoRix</div>
      <div class="brand-tagline">Finance and<br>Accounting</div>
    </div>

    <div class="contact-block">
      <div class="contact-name">Brent Whitlow</div>
      <div class="contact-role">Director VelmoRix Pty. Ltd.</div>
      <div class="contact-line">M: 0413 582 947</div>
      <div class="contact-line">E: brentwhitlow.rix@mailpost.example</div>
    </div>
  </section>
</body>
</html>
```